Business Card - connecting 2 souls and beggining the journey of self discovery

Logo on the front
with tag line

On the back list of services and contact details

Seminars
workshops
Coaching
podcasts

Darren Whitlow
Health & Wellbeing Life Coach
0491 372 615
darren@brightcoreliving.example
brightcoreliving.example

Industry/Entity Type

Life Coaching

Contact Information for Business Card

I like the use of colour from the logo to be used. I'm not a fan of white.

Requirements
Must have
• My tagline: The journey home starts with you
Nice to have
• Use of colour that is in the mind body soul logo

```html
<!DOCTYPE html>
<html lang="en">
<head>
<meta charset="utf-8">
<title>Brightcore Living – Business Card</title>
<link rel="stylesheet" href="https://fonts.googleapis.com/css2?family=Open+Sans:wght@400;600;700&display=swap">
<style>
  :root {
    --stage: #2b2624;
    --card-black: #050505;
    --card-glow: #262626;
    --violet: #8e3fd0;
    --text-white: #ffffff;
    --text-grey: #a3a3a3;
    --text-soft: #8a8a8a;
    --edge-light: #d8d8d8;
    --mark-fill: #8e3fd0;
  }
  html, body {
    margin: 0;
    width: 1200px;
    height: 844px;
    overflow: hidden;
    background: var(--stage);
    font-family: "Open Sans", Arial, sans-serif;
  }
  .canvas {
    position: relative;
    width: 1200px;
    height: 844px;
  }
  .card {
    position: absolute;
    top: 273px;
    width: 520px;
    height: 298px;
    background: var(--card-black);
    overflow: hidden;
    box-shadow: 0 10px 30px rgba(0,0,0,.45);
  }
  /* Back of card: contact details */
  .card-back { left: 50px; }
  .band {
    position: absolute;
    left: 0;
    width: 100%;
    height: 14px;
    background: var(--violet);
  }
  .band-top { top: 12px; }
  .band-bottom { bottom: 12px; }
  .contact {
    position: absolute;
    inset: 48px 0 0 0;
    text-align: center;
    color: var(--text-white);
  }
  .contact-name {
    margin: 0;
    font-size: 18px;
    font-weight: 700;
    letter-spacing: .2px;
  }
  .contact-role {
    margin: 2px 0 22px;
    font-size: 12.5px;
  }
  .contact-lines {
    list-style: none;
    margin: 0;
    padding: 0;
    font-size: 13px;
    line-height: 19px;
  }
  .services {
    position: absolute;
    left: 0;
    right: 0;
    bottom: 50px;
    display: flex;
    justify-content: center;
    align-items: center;
    gap: 12px;
    margin: 0;
    padding: 0;
    list-style: none;
    color: var(--text-white);
    font-size: 14px;
    font-weight: 700;
  }
  .services li + li::before {
    content: "";
    display: inline-block;
    width: 7px;
    height: 7px;
    margin-right: 12px;
    border-radius: 50%;
    background: var(--text-white);
    vertical-align: middle;
  }
  /* Front of card: brand */
  .card-front {
    left: 630px;
    background: radial-gradient(ellipse at 50% 42%, var(--card-glow) 0%, var(--card-black) 62%);
  }
  .edge-tab {
    position: absolute;
    width: 28px;
    height: 36px;
    background: var(--violet);
  }
  .edge-tab::after {
    content: "";
    position: absolute;
    top: 0;
    width: 3px;
    height: 100%;
    background: var(--edge-light);
  }
  .edge-tab-right { right: 0; top: 44px; }
  .edge-tab-right::after { left: 0; }
  .edge-tab-left { left: 0; top: 172px; }
  .edge-tab-left::after { right: 0; }
  .brand {
    position: absolute;
    inset: 0;
    display: flex;
    flex-direction: column;
    align-items: center;
    justify-content: center;
    padding-bottom: 4px;
  }
  .brand-mark {
    width: 84px;
    height: 84px;
    border-radius: 50%;
    background: var(--mark-fill);
  }
  .brand-name {
    margin: 20px 0 0;
    font-size: 30px;
    font-weight: 400;
    line-height: 1.2;
    color: var(--text-grey);
    letter-spacing: -.5px;
  }
  .brand-tagline {
    margin: 6px 0 0;
    font-size: 13px;
    font-weight: 400;
    color: var(--text-soft);
    letter-spacing: .3px;
  }
</style>
</head>
<body>
<main class="canvas">
  <section class="card card-back" aria-label="Business card back">
    <div class="band band-top"></div>
    <div class="contact">
      <h1 class="contact-name">Darren Whitlow</h1>
      <p class="contact-role">Health &amp; Wellbeing Life Coach</p>
      <ul class="contact-lines">
        <li>0491 372 615</li>
        <li>darren@brightcoreliving.example</li>
        <li>www.brightcoreliving.example</li>
      </ul>
    </div>
    <ul class="services">
      <li>Seminars</li>
      <li>Workshops</li>
      <li>Coaching</li>
      <li>Podcasts</li>
    </ul>
    <div class="band band-bottom"></div>
  </section>

  <section class="card card-front" aria-label="Business card front">
    <div class="edge-tab edge-tab-right"></div>
    <div class="edge-tab edge-tab-left"></div>
    <div class="brand">
      <div class="brand-mark"></div>
      <p class="brand-name">Brightcore Living</p>
      <p class="brand-tagline">The journey home starts with you</p>
    </div>
  </section>
</main>
</body>
</html>
```